Business Card Design Project - del varosi group

dear Sirs

we need business card design for our group ( DEL Varosi Group ) , i have got the Logo design of our group from pixel harbor in previous , so all need details relating to our group i think available with you, as well as the the chosen logo design

we hope to provide us with business card logo that to be appropaite and satisfactory to us .

thanks

note : logo design of our group is attached .
Updates

Reason: please extend the deadline of my project for additional 15 days because i didn't received appropriate design for our gruop yet . kindly beaware that i have received 77 design till now , supossed to send me 200-250 design at least . thanks

Target Market(s)

contents

name : Kerem EL Nadiri

position : Operation Manager

Industry/Entity Type

Business

Requirements
Must have

• person name

group logo
Nice to have
• logo color matching with back background

```html
<!DOCTYPE html>
<html lang="en">
<head>
<meta charset="utf-8">
<title>DEL Varosi Group – Business Card</title>
<link href="https://fonts.googleapis.com/css2?family=Source+Sans+3:wght@400;600&display=swap" rel="stylesheet">
<style>
  :root {
    --stage: #dcdde0;
    --blue-deep: #0f3f86;
    --blue-mid: #1f5fae;
    --blue-light: #4aa0dc;
    --ink-blue: #1b4f9c;
    --ink-dark: #0d1b33;
    --gold: #e0b04a;
    --cream: #f1e7d2;
    --white: #ffffff;
  }
  * { margin: 0; padding: 0; box-sizing: border-box; }
  html, body {
    width: 1200px; height: 900px; overflow: hidden;
    background: var(--stage);
    font-family: "Source Sans 3", "Helvetica Neue", Arial, sans-serif;
  }
  .sheet {
    width: 1200px; height: 900px;
    display: flex; flex-direction: column; align-items: center; justify-content: center;
    gap: 34px;
  }
  .card {
    position: relative; width: 700px; height: 400px; overflow: hidden;
    box-shadow: 0 6px 18px rgba(0,0,0,.18);
  }
  .card-art { position: absolute; inset: 0; }

  /* Back side */
  .card-back { background: var(--blue-deep); }
  .back-wordmark {
    position: absolute; left: 0; right: 0; top: 138px;
    display: flex; align-items: center; justify-content: center; gap: 14px;
    color: var(--white); font-weight: 600; font-size: 50px; letter-spacing: 1px;
  }
  .wordmark-square { width: 26px; height: 26px; background: var(--white); }
  .back-web {
    position: absolute; left: 0; right: 0; top: 262px; text-align: center;
    color: var(--gold); font-size: 20px; letter-spacing: .5px;
  }

  /* Front side */
  .card-front { background: var(--white); }
  .front-wordmark {
    position: absolute; left: 34px; top: 150px;
    display: flex; align-items: center; gap: 12px;
    color: var(--ink-blue); font-weight: 600; font-size: 38px;
  }
  .front-wordmark .wordmark-square { width: 20px; height: 20px; background: var(--ink-blue); }
  .address {
    position: absolute; left: 48px; bottom: 36px;
    color: var(--ink-blue); font-weight: 600; font-size: 20px; line-height: 1.15;
  }
  .person { position: absolute; right: 52px; top: 38px; text-align: left; width: 250px; }
  .person-name { color: var(--white); font-size: 28px; }
  .person-role { color: var(--ink-dark); font-size: 18px; font-weight: 600; margin-top: 2px; }
  .contacts {
    position: absolute; right: 22px; top: 190px;
    list-style: none; display: flex; flex-direction: column; align-items: flex-end; gap: 7px;
  }
  .contact {
    display: flex; align-items: center; gap: 10px;
    color: var(--white); font-size: 19px; letter-spacing: .3px;
  }
  .contact svg { width: 22px; height: 22px; flex: none; }
</style>
</head>
<body>
<main class="sheet">

  <section class="card card-back" aria-label="Card back">
    <svg class="card-art" viewBox="0 0 700 400" aria-hidden="true">
      <defs>
        <linearGradient id="backGrad" x1="0" y1="0" x2="1" y2="1">
          <stop offset="0" stop-color="#2b7fd0"/>
          <stop offset=".55" stop-color="#1a5cb0"/>
          <stop offset="1" stop-color="#0f3f86"/>
        </linearGradient>
      </defs>
      <rect width="700" height="400" fill="url(#backGrad)"/>
      <path d="M0,70 C200,20 450,10 700,60 L700,0 L0,0 Z" fill="#ffffff" opacity=".07"/>
      <path d="M0,250 C220,180 470,170 700,230 L700,290 C470,230 220,240 0,310 Z" fill="#ffffff" opacity=".06"/>
      <path d="M0,340 C240,290 470,300 700,360 L700,400 L0,400 Z" fill="#000000" opacity=".08"/>
    </svg>
    <div class="back-wordmark"><span class="wordmark-square"></span>DEL Varosi Group</div>
    <p class="back-web">www.delvarosi.com</p>
  </section>

  <section class="card card-front" aria-label="Card front">
    <svg class="card-art" viewBox="0 0 700 400" aria-hidden="true">
      <defs>
        <linearGradient id="panelGrad" x1="0" y1="0" x2="0" y2="1">
          <stop offset="0" stop-color="#5aaee3"/>
          <stop offset=".45" stop-color="#2a78c6"/>
          <stop offset="1" stop-color="#124a98"/>
        </linearGradient>
      </defs>
      <path d="M0,300 C120,240 260,250 380,300 L380,330 C260,285 120,280 0,340 Z" fill="#f1e7d2" opacity=".8"/>
      <path d="M0,250 C140,200 270,215 370,250 L360,265 C260,235 140,225 0,275 Z" fill="#f1e7d2" opacity=".55"/>
      <path d="M0,360 C130,320 260,330 400,370 L400,400 L0,400 Z" fill="#f1e7d2" opacity=".45"/>
      <path d="M264,0 C360,110 410,250 420,400 L700,400 L700,0 Z" fill="#9aa7b5" opacity=".5" transform="translate(-4,0)"/>
      <path d="M264,0 C360,110 410,250 420,400 L700,400 L700,0 Z" fill="url(#panelGrad)"/>
    </svg>

    <div class="front-wordmark"><span class="wordmark-square"></span>DEL Varosi Group</div>

    <p class="address">P.O. Box: 48210<br>Dubai<br>United Arab Emirates</p>

    <div class="person">
      <p class="person-name">Kerem EL Nadiri</p>
      <p class="person-role">Operation Manager</p>
    </div>

    <ul class="contacts">
      <li class="contact">+971 . 455 . 0142
        <svg viewBox="0 0 22 22" aria-label="Telephone"><circle cx="11" cy="11" r="10" fill="#fff"/><path d="M5,9 Q11,4 17,9 L15,11 L13,9 L9,9 L7,11 Z M7,12 H15 V16 H7 Z" fill="#1f5fae"/></svg>
      </li>
      <li class="contact">+971 . 455 . 0143
        <svg viewBox="0 0 22 22" aria-label="Mobile"><circle cx="11" cy="11" r="10" fill="#fff"/><rect x="8" y="5" width="6" height="12" rx="1.2" fill="#1f5fae"/><rect x="9" y="6.5" width="4" height="6" fill="#fff"/></svg>
      </li>
      <li class="contact">+971 . 455 . 0144
        <svg viewBox="0 0 22 22" aria-label="Fax"><circle cx="11" cy="11" r="10" fill="#fff"/><rect x="6" y="9" width="10" height="7" rx="1" fill="#1f5fae"/><rect x="8" y="5" width="6" height="5" fill="#1f5fae"/></svg>
      </li>
      <li class="contact">info@delvarosi.com
        <svg viewBox="0 0 22 22" aria-label="Email"><circle cx="11" cy="11" r="10" fill="#fff"/><rect x="5.5" y="7.5" width="11" height="7.5" fill="#1f5fae"/><path d="M5.5,7.5 L11,12 L16.5,7.5" fill="none" stroke="#fff" stroke-width="1"/></svg>
      </li>
      <li class="contact">www.delvarosi.com
        <svg viewBox="0 0 22 22" aria-label="Website"><circle cx="11" cy="11" r="10" fill="#fff"/><circle cx="11" cy="11" r="6" fill="none" stroke="#1f5fae" stroke-width="1.3"/><ellipse cx="11" cy="11" rx="2.6" ry="6" fill="none" stroke="#1f5fae" stroke-width="1.1"/><path d="M5,11 H17" stroke="#1f5fae" stroke-width="1.1"/></svg>
      </li>
    </ul>
  </section>

</main>
</body>
</html>
```